business card for horse saddlery

after a new business card for our saddlery, i will add 2 logos we have previously used and they can be used (or not) . Any images can be used from our website also at www.harrowfields.net.au, I have also added our brand logo, which may be good to incorporate on back ? we have over 15, 000 items online, ship Australia Wide.

Target Market(s)

horse owners

Industry/Entity Type

Retail - Equestrian

Contact Information for Business Card

Harrowfield Horse Supplies, 1300 48 62 90, www.harrowfields.net.au, 27 Lindqvist Rd Marrowbank Q 4587

Requirements
Must have
• trailgem is our brand so trailgem logo on back as 'distributers of', easy to read
Nice to have
• professional but fun
Should not have
• double sided (description wont save double sided)

```html
<!DOCTYPE html>
<html lang="en">
<head>
<meta charset="utf-8">
<title>Harrowfield Horse Supplies – Business Card</title>
<link rel="stylesheet" href="https://fonts.googleapis.com/css2?family=Open+Sans:wght@400;600;800&display=swap">
<style>
  :root {
    --stage: #232323;
    --paper: #ffffff;
    --amber: #fbb21f;
    --navy: #253b8a;
    --sky: #3fb3e6;
    --ink: #1b1b1b;
    --photo-dark: #0d0d0d;
    --photo-light: #c9ccd0;
  }
  * { margin: 0; padding: 0; box-sizing: border-box; }
  html, body { width: 1200px; height: 780px; overflow: hidden; background: var(--stage); }
  body { font-family: "Open Sans", Arial, sans-serif; position: relative; }

  .card {
    position: absolute;
    width: 540px; height: 310px;
    background: var(--paper);
    border-radius: 22px;
    overflow: hidden;
    box-shadow: 0 5px 0 var(--amber), 0 18px 30px rgba(0,0,0,.55);
  }
  .card--front { left: 40px; top: 235px; }
  .card--back  { left: 620px; top: 235px; }

  /* Front: brand name */
  .brand-front {
    position: absolute; inset: 0;
    display: flex; align-items: center; justify-content: center; gap: 18px;
  }
  .brand-dot {
    width: 74px; height: 74px; border-radius: 50%;
    background: var(--amber); flex: none;
  }
  .brand-name {
    color: var(--navy); font-weight: 600; line-height: 1.1;
    font-size: 34px;
  }
  .brand-name span { display: block; font-size: 22px; }

  /* Back */
  .back-art { position: absolute; inset: 0; }
  .back-brand {
    position: absolute; left: 30px; top: 26px;
    display: flex; align-items: center; gap: 10px;
  }
  .back-brand .brand-dot { width: 40px; height: 40px; }
  .back-brand .brand-name { font-size: 19px; }
  .back-brand .brand-name span { font-size: 12px; }

  .holder {
    position: absolute; right: 38px; top: 18px; text-align: right;
  }
  .holder-name { font-weight: 800; font-size: 25px; line-height: 1.1; }
  .holder-first { color: var(--amber); }
  .holder-last { color: var(--navy); }
  .holder-role { font-size: 13px; color: var(--ink); font-weight: 600; }

  .contact {
    position: absolute; left: 34px; top: 118px; color: var(--ink);
  }
  .contact-address { font-size: 14px; font-weight: 600; line-height: 1.35; margin-bottom: 8px; }
  .contact-row { display: flex; align-items: center; gap: 8px; }
  .contact-phone { font-size: 22px; font-weight: 600; }
  .contact-web { font-size: 14px; font-weight: 600; }
  .contact-icon { width: 18px; height: 18px; flex: none; }

  .partners {
    position: absolute; right: 26px; bottom: 36px;
    display: flex; gap: 22px; align-items: center;
  }
  .partner-name { color: var(--navy); font-weight: 600; font-size: 16px; }
  .partner-label { color: var(--navy); font-size: 10px; font-weight: 600; display: block; text-transform: uppercase; letter-spacing: .5px; }
</style>
</head>
<body>

  <section class="card card--front" aria-label="Card front">
    <div class="brand-front">
      <div class="brand-dot"></div>
      <div class="brand-name">Harrowfield<span>Horse Supplies</span></div>
    </div>
  </section>

  <section class="card card--back" aria-label="Card back">
    <svg class="back-art" viewBox="0 0 540 310" width="540" height="310" aria-hidden="false">
      <defs>
        <linearGradient id="swoosh" x1="0" x2="1" y1="0" y2="0">
          <stop offset="0" stop-color="var(--navy)"/>
          <stop offset="1" stop-color="var(--sky)"/>
        </linearGradient>
        <radialGradient id="photo" cx="0.55" cy="0.55" r="0.6">
          <stop offset="0" stop-color="var(--photo-light)"/>
          <stop offset="0.6" stop-color="#6d6f73"/>
          <stop offset="1" stop-color="var(--photo-dark)"/>
        </radialGradient>
      </defs>
      <!-- amber wave -->
      <path d="M0,310 L0,278 C120,300 250,270 310,200 C360,140 390,105 540,95 L540,310 Z" fill="var(--amber)"/>
      <!-- blue swoosh -->
      <path d="M80,262 C160,282 250,262 300,222 C260,268 170,285 84,272 Z" fill="url(#swoosh)"/>
      <!-- top-right amber tab -->
      <rect x="500" y="0" width="40" height="28" fill="var(--amber)"/>
      <!-- photo area -->
      <circle cx="418" cy="128" r="66" fill="var(--paper)"/>
      <circle cx="418" cy="128" r="62" fill="url(#photo)" role="img" aria-label="Photo of a grey horse in a bridle on a dark background"/>
    </svg>

    <div class="back-brand">
      <div class="brand-dot"></div>
      <div class="brand-name">Harrowfield<span>Horse Supplies</span></div>
    </div>

    <div class="holder">
      <div class="holder-name"><span class="holder-first">Lenka</span> <span class="holder-last">Marovic</span></div>
      <div class="holder-role">Horse owners</div>
    </div>

    <div class="contact">
      <p class="contact-address">27 Lindqvist Rd<br>Marrowbank Q 4587</p>
      <div class="contact-row">
        <svg class="contact-icon" viewBox="0 0 20 20" aria-hidden="true">
          <circle cx="10" cy="10" r="10" fill="var(--sky)"/>
          <path d="M6.5 5.5 l2 -0.5 l1 2.5 l-1.2 1 a6 6 0 0 0 3.2 3.2 l1 -1.2 l2.5 1 l-0.5 2 c-4 0.5 -8.5 -4 -8 -8z" fill="#fff"/>
        </svg>
        <span class="contact-phone">1300 48 62 90</span>
      </div>
      <div class="contact-row">
        <svg class="contact-icon" viewBox="0 0 20 20" aria-hidden="true">
          <circle cx="10" cy="10" r="10" fill="var(--sky)"/>
          <circle cx="10" cy="10" r="5.5" fill="none" stroke="#fff" stroke-width="1.4"/>
          <path d="M4.5 10 h11 M10 4.5 c-3 3 -3 8 0 11 M10 4.5 c3 3 3 8 0 11" fill="none" stroke="#fff" stroke-width="1"/>
        </svg>
        <span class="contact-web">www.harrowfields.net.au</span>
      </div>
    </div>

    <div class="partners">
      <div class="partner-name"><span class="partner-label">Distributors of</span>trailgem</div>
      <div class="partner-name">Harrowfield</div>
    </div>
  </section>

</body>
</html>
```